Business Card Design for company

We want new business cards. We'd like something different-- yet still highly professional. Our tagline is Providing leadership, delivering success. Stock photos are ok, as long as they are relevant and look upscale.

Target Market(s)

Architecture/Business Management Consulting/Engineering Consulting

Contact Information for Business Card

dark gray background with pops of blue might be good, but you tell me. You're the designers. Rounded corners might be nice, but again, you tell me.

Font styles to use
Serif
Sans Serif

Colors
3276b5
5c5c5c
9d9d9d
fbfbfb

Requirements
Nice to have
• Something different, but still very professional.

```html
<!DOCTYPE html>
<html lang="en">
<head>
<meta charset="utf-8">
<title>Norvale International – Business Cards</title>
<link rel="stylesheet" href="https://fonts.googleapis.com/css2?family=Montserrat:wght@300;400;500;600&display=swap">
<style>
  :root {
    --brand-blue: #3276b5;
    --graphite: #5c5c5c;
    --silver: #9d9d9d;
    --paper: #fbfbfb;
    --stage: #0c0c0d;
    --card-top: #232325;
    --card-bottom: #141415;
  }
  * { margin: 0; padding: 0; box-sizing: border-box; }
  html, body { width: 1200px; height: 890px; overflow: hidden; background: var(--stage); }
  body { font-family: "Montserrat", sans-serif; color: var(--paper); }

  .canvas {
    position: relative; width: 1200px; height: 890px;
    display: flex; flex-direction: column; align-items: center; justify-content: center; gap: 40px;
  }
  .card {
    position: relative; width: 700px; height: 400px; border-radius: 22px;
    background: linear-gradient(155deg, var(--card-top) 0%, var(--card-bottom) 100%);
    overflow: hidden;
  }

  /* Front */
  .card--front { display: flex; flex-direction: column; align-items: center; justify-content: center; }
  .wordmark { display: flex; align-items: center; gap: 16px; }
  .wordmark__square { width: 22px; height: 22px; background: var(--brand-blue); flex: none; }
  .wordmark__name {
    font-weight: 500; font-size: 30px; letter-spacing: 6px; color: var(--silver);
    text-transform: uppercase; white-space: nowrap;
  }
  .tagline {
    margin-top: 26px; font-weight: 400; font-size: 13px; letter-spacing: 3.5px;
    color: var(--silver); text-transform: uppercase; white-space: nowrap;
  }

  /* Back */
  .card--back .wordmark { position: absolute; top: 60px; right: 60px; }
  .card--back .wordmark__name { font-size: 20px; letter-spacing: 4px; }
  .card--back .wordmark__square { width: 15px; height: 15px; }

  .person { position: absolute; left: 60px; top: 170px; width: 250px; }
  .person__name {
    font-weight: 600; font-size: 24px; letter-spacing: 2px; color: var(--brand-blue);
    text-transform: uppercase; white-space: nowrap;
  }
  .person__role { margin-top: 8px; font-weight: 300; font-size: 16px; letter-spacing: 1px; color: var(--silver); }

  .divider { position: absolute; left: 330px; top: 165px; width: 1px; height: 130px; background: var(--brand-blue); }

  .contact { position: absolute; left: 360px; top: 168px; list-style: none; }
  .contact__item {
    display: flex; align-items: center; gap: 12px; height: 30px;
    font-size: 14px; font-weight: 400; letter-spacing: 0.6px; color: var(--paper); white-space: nowrap;
  }
  .contact__icon { width: 14px; height: 14px; flex: none; }

  .address {
    position: absolute; left: 60px; bottom: 50px; font-size: 14px; font-weight: 300;
    letter-spacing: 0.8px; color: var(--silver); white-space: nowrap;
  }
</style>
</head>
<body>
<main class="canvas">

  <section class="card card--front" aria-label="Card front">
    <div class="wordmark">
      <span class="wordmark__square"></span>
      <span class="wordmark__name">Norvale International</span>
    </div>
    <p class="tagline">Guiding Vision | Building Results</p>
  </section>

  <section class="card card--back" aria-label="Card back">
    <div class="wordmark">
      <span class="wordmark__square"></span>
      <span class="wordmark__name">Norvale International</span>
    </div>

    <div class="person">
      <p class="person__name">Daniel Ostrow</p>
      <p class="person__role">Design Consultant</p>
    </div>

    <div class="divider"></div>

    <ul class="contact">
      <li class="contact__item">
        <svg class="contact__icon" viewBox="0 0 16 16" aria-hidden="true"><path fill="#3276b5" d="M3.5 1.5l2.5 0 1 3.5-1.7 1.2a8 8 0 0 0 4.5 4.5l1.2-1.7 3.5 1v2.5c0 .8-.7 1.5-1.5 1.5A12.5 12.5 0 0 1 2 3c0-.8.7-1.5 1.5-1.5z"/></svg>
        +1 555-014-2290
      </li>
      <li class="contact__item">
        <svg class="contact__icon" viewBox="0 0 16 16" aria-hidden="true"><rect x="1" y="3" width="14" height="10" rx="1.5" fill="#3276b5"/><path d="M1.5 4l6.5 5 6.5-5" fill="none" stroke="#141415" stroke-width="1.2"/></svg>
        MARKETING@NORVALEINTL.COM
      </li>
      <li class="contact__item">
        <svg class="contact__icon" viewBox="0 0 16 16" aria-hidden="true"><rect x="1" y="3" width="14" height="10" rx="1.5" fill="#3276b5"/><path d="M1.5 4l6.5 5 6.5-5" fill="none" stroke="#141415" stroke-width="1.2"/></svg>
        INFO@NORVALEINTL.COM
      </li>
      <li class="contact__item">
        <svg class="contact__icon" viewBox="0 0 16 16" aria-hidden="true"><circle cx="8" cy="8" r="6.5" fill="none" stroke="#3276b5" stroke-width="1.4"/><ellipse cx="8" cy="8" rx="2.8" ry="6.5" fill="none" stroke="#3276b5" stroke-width="1.2"/><path d="M1.5 8h13" stroke="#3276b5" stroke-width="1.2"/></svg>
        www.norvaleintl.com
      </li>
    </ul>

    <p class="address">1450 Harbor Crest Lane Tampa, FL 33602</p>
  </section>

</main>
</body>
</html>
```